Vitamin B12 Liquid Drops Label

hi, i need a label designed for my vitamin b12 drops that i am going to be selling on shopzello. the label needs to quickly capture the attention of a buyer as he or she is scrolling through the thumbnail search results on shopzello.com my brand is called nralo. i already have an example brand logo i will be using, however, i need help designing the rest of the label. attached are some examples of labels i like for other supplements.some of these examples are pink. i do not want pink. please go for a blue/green color scheme. THE DESIGN MUST BE BOLD

Target Market(s)

adults ages 30 - 64

Font styles to use
Sans Serif

Colors
0455a3
cedeed
3176b5
85acd3
cfdeed
9bcb3b
abd037
cadf82
00a990

Requirements
Must have
• - bold design
• - somewhat gender-neutral color scheme because this will be used equally by men and women
• - B12 MUST be very prominent and visible on the label
Should not have
• - it should not be "crunchy" looking

```html
<!DOCTYPE html>
<html lang="en">
<head>
<meta charset="utf-8">
<title>nralo Vitamin B12 Label</title>
<link rel="stylesheet" href="https://fonts.googleapis.com/css2?family=Ubuntu:wght@500;700&display=swap">
<style>
  :root {
    --canvas: #ffffff;
    --label-blue: #0455a3;
    --label-green: #9bcb3b;
    --ink-navy: #0455a3;
    --ink-lime: #cadf82;
    --ink-teal-light: #cfdeed;
  }
  * { margin: 0; padding: 0; box-sizing: border-box; }
  html, body {
    width: 1200px;
    height: 900px;
    overflow: hidden;
    background: var(--canvas);
  }
  .canvas {
    position: relative;
    width: 1200px;
    height: 900px;
    background: var(--canvas);
  }
  .label {
    position: absolute;
    left: 300px;
    top: 67px;
    width: 600px;
    height: 766px;
    background: var(--label-blue);
    overflow: hidden;
    font-family: "Ubuntu", sans-serif;
  }
  .label-band {
    position: absolute;
    inset: 0;
    width: 100%;
    height: 100%;
  }
  .label-band .green-field { fill: var(--label-green); }
  .product-name {
    position: absolute;
    left: 20px;
    top: 330px;
    font-weight: 700;
    font-size: 68px;
    line-height: 1;
    letter-spacing: 1px;
    color: var(--ink-navy);
    white-space: nowrap;
  }
  .product-form {
    position: absolute;
    left: 28px;
    top: 424px;
    font-weight: 700;
    font-size: 22px;
    letter-spacing: 10px;
    color: var(--ink-lime);
    white-space: nowrap;
  }
  .brand-name {
    position: absolute;
    right: 30px;
    top: 610px;
    font-weight: 700;
    font-size: 92px;
    line-height: 1;
    color: var(--ink-lime);
    white-space: nowrap;
  }
</style>
</head>
<body>
  <main class="canvas">
    <section class="label" aria-label="Vitamin B12 drops label">
      <svg class="label-band" viewBox="0 0 600 766" preserveAspectRatio="none" aria-hidden="true">
        <polygon class="green-field" points="0,0 600,0 456,400 0,400"/>
      </svg>
      <h1 class="product-name">VITAMIN B12</h1>
      <p class="product-form">METHYLCOBAMALIN</p>
      <p class="brand-name">nralo</p>
    </section>
  </main>
</body>
</html>
```